Business Card Design for company

We want new business cards. We'd like something different-- yet still highly professional. Our tagline is Providing leadership, delivering success. Stock photos are ok, as long as they are relevant and look upscale.

Target Market(s)

Architecture/Business Management Consulting/Engineering Consulting

Contact Information for Business Card

dark gray background with pops of blue might be good, but you tell me. You're the designers. Rounded corners might be nice, but again, you tell me.

Font styles to use
Serif
Sans Serif

Colors
3276b5
5c5c5c
9d9d9d
fbfbfb

Requirements
Nice to have
• Something different, but still very professional.

```html
<!DOCTYPE html>
<html lang="en">
<head>
<meta charset="utf-8">
<title>Norvale Group — Business Card</title>
<link rel="stylesheet" href="https://fonts.googleapis.com/css2?family=Oswald:wght@500&family=Work+Sans:wght@400;500;600&display=swap">
<style>
  :root {
    --stage: #1c1c1c;
    --card: #232323;
    --card-edge: #2c2c2c;
    --blue: #3276b5;
    --white: #fbfbfb;
    --grey: #9d9d9d;
    --grey-dark: #5c5c5c;
  }
  * { box-sizing: border-box; margin: 0; padding: 0; }
  html, body { width: 1200px; height: 900px; overflow: hidden; }
  body {
    background: radial-gradient(ellipse at 60% 40%, #2a2a2a 0%, var(--stage) 70%);
    font-family: "Work Sans", sans-serif;
    color: var(--white);
    position: relative;
  }
  .card {
    position: absolute;
    left: 290px;
    width: 620px;
    height: 354px;
    background: linear-gradient(135deg, var(--card) 0%, var(--card-edge) 100%);
    box-shadow: 0 14px 30px rgba(0,0,0,.55);
  }
  .card--front { top: 70px; }
  .card--back { top: 476px; }

  /* front */
  .brand {
    position: absolute;
    top: 112px; left: 0; right: 0;
    text-align: center;
    display: flex; justify-content: center; align-items: center; gap: 14px;
  }
  .brand__mark { width: 18px; height: 18px; background: var(--blue); }
  .brand__name {
    font-weight: 600;
    font-size: 42px;
    letter-spacing: 4px;
    color: var(--white);
  }
  .front__web {
    position: absolute;
    top: 262px; left: 0; right: 0;
    display: flex; justify-content: center; align-items: center; gap: 12px;
    font-size: 14px; letter-spacing: .5px;
  }
  .front__rule { width: 104px; height: 1px; background: var(--blue); }

  /* back */
  .person {
    position: absolute;
    top: 118px; right: 348px;
    text-align: right;
  }
  .person__name {
    font-family: "Oswald", sans-serif;
    font-weight: 500;
    font-size: 34px;
    letter-spacing: 1.5px;
    color: var(--blue);
    text-transform: uppercase;
    line-height: 1.1;
  }
  .person__role { font-size: 15px; margin-top: 4px; letter-spacing: .5px; }
  .divider {
    position: absolute;
    top: 120px; left: 292px;
    width: 1.5px; height: 64px;
    background: var(--white);
  }
  .contacts {
    position: absolute;
    top: 118px; left: 318px;
    list-style: none;
    font-size: 15px; letter-spacing: .4px;
  }
  .contacts li { display: flex; align-items: center; gap: 10px; height: 23px; }
  .contacts svg { width: 11px; height: 11px; flex: none; }
  .address {
    position: absolute;
    bottom: 52px; left: 0; right: 0;
    text-align: center;
    font-size: 15px; letter-spacing: .6px;
  }
</style>
</head>
<body>
  <section class="card card--front" aria-label="Card front">
    <div class="brand">
      <span class="brand__mark"></span>
      <span class="brand__name">NORVALE GROUP</span>
    </div>
    <div class="front__web">
      <span class="front__rule"></span>
      <span>www.norvalegroup.com</span>
      <span class="front__rule"></span>
    </div>
  </section>

  <section class="card card--back" aria-label="Card back">
    <div class="person">
      <p class="person__name">Daniel Carver</p>
      <p class="person__role">Director</p>
    </div>
    <span class="divider"></span>
    <ul class="contacts">
      <li>
        <svg viewBox="0 0 12 12" aria-hidden="true"><path d="M2.5 1h2l1 2.5-1.3 1a6 6 0 0 0 3.3 3.3l1-1.3 2.5 1v2a1 1 0 0 1-1 1A9.5 9.5 0 0 1 1.5 2a1 1 0 0 1 1-1z" fill="var(--blue)"/></svg>
        (555) 014-2290
      </li>
      <li>
        <svg viewBox="0 0 12 12" aria-hidden="true"><rect x="1" y="2.5" width="10" height="7" fill="none" stroke="var(--blue)" stroke-width="1"/><path d="M1 2.5l5 4 5-4" fill="none" stroke="var(--blue)" stroke-width="1"/></svg>
        info@norvalegroup.com
      </li>
      <li>
        <svg viewBox="0 0 12 12" aria-hidden="true"><circle cx="6" cy="6" r="5" fill="none" stroke="var(--blue)" stroke-width="1"/><ellipse cx="6" cy="6" rx="2.2" ry="5" fill="none" stroke="var(--blue)" stroke-width="1"/><path d="M1 6h10" stroke="var(--blue)" stroke-width="1"/></svg>
        www.norvalegroup.com
      </li>
    </ul>
    <p class="address">48 Harbour Lane, Westfield, NZ, 8020</p>
  </section>
</body>
</html>
```